General Surgeon flyer to be distributed to GPs

I am a general surgeon and I would like to have a flyer designed aiming to introduce myself to GPs.

Name: Dr Tobias Lindqvar MD, FRACS
Address: Suite 4C, Brellam private hospital, 418 Corvell Parade, Harlowe, VIC, 3188
T: (03) 9587 6102
F: (03) 9463 1178
E: referrals@quillfordsurgeons.com.au
Website: www.quillfordsurgeons.com.au

Tobias is a highly trained general surgeon, having completed extensive surgical training at Tarrowby health, Pellington and Corrigan Health networks. He further specialized by completing a fellowship in Oesophagogastric and Bariatric Surgery at St Aldric’s Hospital Melbourne, one of Victoria’s leading Upper GI surgical centres.

With expertise in both advanced laparoscopic and open surgical techniques, he performs a wide range of procedures involving the gastrointestinal system, abdominal wall hernias, as well as other major and minor general surgical operations. In addition to holding appointments at Tarrowby Health, he also operates at Brellam and Fernwick Private Hospitals.

Dr Lindqvar is committed to providing patient-centred care with a focus on surgical precision, safety, and long-term health outcomes.

He is also fluent in Farsi/Pesrian.
Outside of surgery, Tobias enjoys playings classical piano and spending time with his 6-year-old Bordoodle on long walks.

Upper GI & Bariatric Surgery:
Hiatus hernia repair, sleeve gastrectomy, gastric bypass
General Surgery conditions:
Gallbladder Surgery: Laparoscopic cholecystectomy
Hernia Repair: Laparoscopic and open surgery (inguinal,
umbilical, incisional)
Anorectal Procedures: Haemorrhoidectomy, haemorrhoid banding
Hand Surgery: Carpal tunnel release, Lymph Node Biopsy
Ingrown Toenail Surgery
Skin & Soft Tissue Surgery: Skin cancer removal, lipoma and
sebaceous cyst excision
Emergency Surgery: Laparotomy, Appendicectomy, bowel resection
Endoscopy: Diagnostic and therapeutic procedures

```html
<!DOCTYPE html>
<html lang="en">
<head>
<meta charset="utf-8">
<title>Dr Tobias Lindqvar – General Surgeon</title>
<link href="https://fonts.googleapis.com/css2?family=Poppins:wght@400;500;600;700;800&family=Allura&display=swap" rel="stylesheet">
<style>
:root{
  --backdrop:#8f8f8f;
  --paper:#ffffff;
  --ink:#2b2b2b;
  --navy:#07506b;
  --green:#2bb24c;
  --sky:#1db3e8;
  --member:#1f4e8c;
}
*{margin:0;padding:0;box-sizing:border-box}
html,body{width:973px;height:1200px;overflow:hidden;background:var(--backdrop)}
body{font-family:'Poppins',sans-serif;color:var(--ink)}
.flyer{position:absolute;left:77px;top:70px;width:820px;height:1060px;background:var(--paper);overflow:hidden}
.abs{position:absolute}

/* brand */
.brand{left:0;width:384px;top:98px;display:flex;align-items:center;justify-content:center;gap:10px}
.brand-mark{width:26px;height:26px;border-radius:50%;background:var(--sky)}
.brand-name{font-weight:600;font-size:22px;color:var(--navy);line-height:1}

/* name */
.name{left:0;width:384px;top:196px;text-align:center;font-weight:800;font-size:53px;line-height:52px;letter-spacing:-0.5px;color:var(--ink)}
.creds{left:0;width:384px;top:312px;text-align:center;font-weight:800;font-size:40px;color:var(--green)}

/* contact band */
.contact{left:0;top:387px;width:384px;height:159px;background:var(--navy);border-bottom-right-radius:26px;color:var(--paper)}
.contact .addr{left:99px;top:24px;font-size:12.3px;line-height:15px}
.contact .pin{left:64px;top:25px}
.pill{top:67px;height:22px;width:141px;border-radius:5px;display:flex;align-items:center;gap:8px;padding-left:5px;font-weight:600;font-size:12.5px}
.pill.tel{left:71px;background:var(--sky)}
.pill.fax{left:220px;background:var(--green)}
.pill .ico{width:16px;height:16px;border-radius:3px;background:var(--paper);display:flex;align-items:center;justify-content:center}
.line{left:92px;font-size:12.3px;line-height:16px}
.line.mail{top:103px}.line.web{top:126px}
.contact .ldot{left:70px}

/* services */
.services-title{left:75px;top:573px;font-weight:700;font-size:14.5px}
.services-title span{color:var(--sky)}
.svc-head{left:75px;font-weight:700;font-size:12.4px;color:var(--green)}
.svc{left:75px;display:flex;gap:9px;font-size:11px;line-height:13px;width:300px}
.svc .dot{flex:none;width:21px;height:21px;border-radius:50%;background:radial-gradient(circle at 40% 35%,#3cc3d6,#0f7fa0);border:2px solid #dff3f7}
.svc b{font-weight:600}

/* right side */
.panel{left:384px;top:293px;width:436px;height:635px;background:var(--green);border-bottom-left-radius:40px}
.panel-deco{left:600px;top:500px;width:200px;height:390px;border-radius:90px;background:radial-gradient(ellipse at center,rgba(255,255,255,.09),rgba(255,255,255,0) 70%)}
.photo-frame{left:384px;top:0;width:436px;height:482px;background:var(--paper);border-radius:0 0 218px 218px / 0 0 150px 150px}
.photo{left:414px;top:10px;width:380px;height:441px;border-radius:0 0 190px 190px / 0 0 140px 140px;background:linear-gradient(180deg,#f2f2f2 0%,#e2e2e2 30%,#b9a797 45%,#6d86b8 65%,#34446f 100%)}
.sig{left:452px;top:495px;font-family:'Allura',cursive;font-size:50px;color:var(--paper);line-height:1}
.bio{left:454px;top:556px;width:296px;color:var(--paper);font-size:10.7px;line-height:12.85px}
.bio p+p{margin-top:12.8px}
.bio b{font-weight:700}
.note-tab{left:438px;top:841px;width:318px;height:16px;background:var(--navy);border-radius:6px 6px 0 0}
.note{left:450px;top:841px;width:298px;height:102px;background:var(--navy);border-radius:0 0 20px 20px;color:var(--paper);padding:17px 0 0 25px;font-size:10.6px;line-height:12.9px}
.note b{display:block;font-weight:700;margin-bottom:5px}

/* memberships */
.member-mark{left:435px;top:974px;width:26px;height:26px;background:var(--member)}
.fellow{left:474px;top:977px;font-size:12px;line-height:15px;color:var(--member)}
.badge{left:660px;top:958px;width:68px;height:68px;border-radius:50%;border:3px solid var(--member)}
</style>
</head>
<body>
<main class="flyer">
  <div class="abs brand"><span class="brand-mark"></span><span class="brand-name">Quillford Surgeons</span></div>

  <h1 class="abs name">Dr Tobias<br>Lindqvar</h1>
  <div class="abs creds">MD, FRACS</div>

  <section class="abs contact">
    <svg class="abs pin" width="22" height="32" viewBox="0 0 22 32"><path d="M11 0C5 0 0 5 0 11c0 8 11 21 11 21s11-13 11-21C22 5 17 0 11 0z" fill="#2bb24c"/><circle cx="11" cy="11" r="4" fill="#07506b"/></svg>
    <div class="abs addr">Suite 4C, Brellam private hospital, 418<br>Corvell Parade, Harlowe, VIC, 3188</div>
    <div class="abs pill tel"><span class="ico"><svg width="11" height="11" viewBox="0 0 24 24"><path d="M6.6 10.8a15 15 0 006.6 6.6l2.2-2.2c.3-.3.7-.4 1-.2 1.1.4 2.3.6 3.6.6.6 0 1 .4 1 1V20c0 .6-.4 1-1 1A17 17 0 013 4c0-.6.4-1 1-1h3.5c.6 0 1 .4 1 1 0 1.3.2 2.5.6 3.6.1.3 0 .7-.2 1z" fill="#1db3e8"/></svg></span>(03) 9587 6102</div>
    <div class="abs pill fax"><span class="ico"><svg width="11" height="11" viewBox="0 0 24 24"><rect x="3" y="8" width="18" height="12" rx="2" fill="#2bb24c"/><rect x="7" y="3" width="10" height="6" fill="#2bb24c"/></svg></span>(03) 9463 1178</div>
    <svg class="abs ldot" style="top:105px" width="13" height="11" viewBox="0 0 13 11"><rect width="13" height="11" rx="1.5" fill="#2bb24c"/><path d="M0 1l6.5 5L13 1" stroke="#07506b" fill="none" stroke-width="1.3"/></svg>
    <div class="abs line mail">referrals@quillfordsurgeons.com.au</div>
    <svg class="abs ldot" style="top:127px" width="13" height="13" viewBox="0 0 13 13"><circle cx="6.5" cy="6.5" r="5.8" fill="none" stroke="#2bb24c" stroke-width="1.3"/><path d="M.7 6.5h11.6M6.5.7c-3 3.5-3 8.1 0 11.6M6.5.7c3 3.5 3 8.1 0 11.6" stroke="#2bb24c" fill="none" stroke-width="1"/></svg>
    <div class="abs line web">www.quillfordsurgeons.com.au</div>
  </section>

  <h2 class="abs services-title">OUR <span>SERVICES</span></h2>

  <h3 class="abs svc-head" style="top:605px">UPPER GI &amp; BARIATRIC SURGERY:</h3>
  <div class="abs svc" style="top:624px"><span class="dot"></span><span style="padding-top:3px">Hiatus hernia repair</span></div>
  <div class="abs svc" style="top:647px"><span class="dot"></span><span style="padding-top:3px">Sleeve gastrectomy</span></div>
  <div class="abs svc" style="top:670px"><span class="dot"></span><span style="padding-top:3px">Gastric bypass</span></div>

  <h3 class="abs svc-head" style="top:702px">GENERAL SURGERY CONDITIONS:</h3>
  <div class="abs svc" style="top:721px"><span class="dot" style="margin-top:6px"></span><span><b>Gallbladder Surgery:</b><br>Laparoscopic cholecystectomy</span></div>
  <div class="abs svc" style="top:752px"><span class="dot" style="margin-top:6px"></span><span><b>Hernia Repair:</b><br>Laparoscopic and open surgery (inguinal,<br>umbilical, incisional)</span></div>
  <div class="abs svc" style="top:797px"><span class="dot" style="margin-top:6px"></span><span><b>Anorectal Procedures:</b><br>Haemorrhoidectomy, haemorrhoid banding</span></div>
  <div class="abs svc" style="top:828px"><span class="dot" style="margin-top:6px"></span><span><b>Hand Surgery:</b><br>Carpal tunnel release, Lymph Node Biopsy<br>Ingrown Toenail Surgery</span></div>

  <h3 class="abs svc-head" style="top:880px">INGROWN TOENAIL SURGERY</h3>
  <div class="abs svc" style="top:900px"><span class="dot" style="margin-top:6px"></span><span><b>Skin &amp; Soft Tissue Surgery:</b><br>Skin cancer removal, lipoma and sebaceous<br>cyst excision</span></div>
  <div class="abs svc" style="top:946px"><span class="dot" style="margin-top:6px"></span><span><b>Emergency Surgery:</b><br>Laparotomy, Appendicectomy, bowel resection</span></div>
  <div class="abs svc" style="top:979px"><span class="dot" style="margin-top:6px"></span><span><b>Endoscopy:</b><br>Diagnostic and therapeutic procedures</span></div>

  <div class="abs panel"></div>
  <div class="abs panel-deco" role="img" aria-label="Faint digestive system illustration"></div>
  <div class="abs photo-frame"></div>
  <div class="abs photo" role="img" aria-label="Portrait photograph of Dr Tobias Lindqvar in a suit and tie"></div>

  <div class="abs sig">Tobias</div>
  <div class="abs bio">
    <p><b>is a highly trained general surgeon,</b><br>having completed extensive surgical training at <b>Tarrowby health, Pellington and Corrigan Health networks.</b> He further specialized by completing a fellowship in Oesophagogastric and Bariatric Surgery at St Aldric’s Hospital Melbourne, one of Victoria’s leading Upper GI surgical centres.</p>
    <p>With expertise in both advanced <b>laparoscopic and open surgical techniques,</b> he performs a wide range of procedures involving the gastrointestinal system, abdominal wall hernias, as well as other major and minor general surgical operations. In addition to holding appointments at Tarrowby Health, he also operates at Brellam and Fernwick Private Hospitals.</p>
    <p><b>Dr Lindqvar</b> is committed to providing patient-centred care with a focus on surgical precision, safety, and long-term health outcomes.</p>
  </div>

  <div class="abs note-tab"></div>
  <div class="abs note"><b>He is also fluent in Farsi/Pesrian.</b>Outside of surgery, Tobias enjoys playings<br>classical piano and spending time with his<br>6-year-old Bordoodle on long walks.</div>

  <div class="abs member-mark"></div>
  <div class="abs fellow">Fellow of the Southern<br>College of Surgeons</div>
  <div class="abs badge"></div>
</main>
</body>
</html>
```